Business Card for Professional Photographer

I'm looking for an eye catching modern clean design that compliments my logo/ website fonts & colours.
I specialise in architecture, corporate & commercial photography so I'm marketing to professional clients rather than portrait / wedding clients.

I would prefer to not have a solid black design.

My logo brand guide is as follows :

Main front font. : Reislust
Main font colour : #fff
Slogan front font : Ubuntu Bold
Monogram front font : Venti Medium
Container colour : #fff

I need print ready files in pdf .png & .eps formats.

Included in the files below are some screen grabs as reference to font & colours etc.

```html
<!DOCTYPE html>
<html lang="en">
<head>
<meta charset="utf-8">
<title>Clearline Studio – Business Card</title>
<link rel="stylesheet" href="https://fonts.googleapis.com/css2?family=Lato:wght@300;400;700&display=swap">
<style>
  :root {
    --stage: #e9e7e4;
    --card: #141318;
    --card-back: #17161b;
    --gold: #d1a94a;
    --white: #f4f2ee;
    --rule: #2c2a30;
    --tagline: #bdbab4;
  }
  * { box-sizing: border-box; margin: 0; padding: 0; }
  html, body {
    width: 1200px;
    height: 844px;
    overflow: hidden;
    background: var(--stage);
    font-family: "Lato", sans-serif;
  }
  .stage {
    width: 1200px;
    height: 844px;
    display: flex;
    align-items: center;
    justify-content: center;
    gap: 40px;
  }
  .card {
    position: relative;
    width: 540px;
    height: 309px;
    border-radius: 3px;
    box-shadow: 0 10px 28px rgba(0, 0, 0, 0.25);
    overflow: hidden;
  }

  /* Front side */
  .card-front { background: var(--card); }
  .brand {
    position: absolute;
    top: 58px;
    left: 0;
    right: 0;
    display: flex;
    flex-direction: column;
    align-items: center;
  }
  .brand-row {
    display: flex;
    align-items: center;
    gap: 12px;
  }
  .brand-mark {
    width: 12px;
    height: 12px;
    background: var(--white);
  }
  .brand-name {
    color: var(--white);
    font-weight: 300;
    font-size: 25px;
    letter-spacing: 3px;
  }
  .brand-tagline {
    margin-top: 6px;
    color: var(--tagline);
    font-size: 8.5px;
    letter-spacing: 1.6px;
    margin-left: 24px;
  }
  .rule {
    position: absolute;
    left: 24px;
    right: 24px;
    height: 1px;
    background: var(--rule);
  }
  .rule-top { top: 160px; }
  .contact {
    position: absolute;
    left: 24px;
    right: 24px;
    bottom: 20px;
    color: var(--white);
  }
  .person-name {
    color: var(--gold);
    font-weight: 700;
    font-size: 17px;
    letter-spacing: 0.5px;
  }
  .person-title {
    font-size: 13px;
    margin-top: 1px;
  }
  .contact-rule {
    height: 1px;
    background: var(--rule);
    margin: 9px 0;
  }
  .contact-line {
    font-size: 13px;
    white-space: nowrap;
  }
  .label, .web { color: var(--gold); }
  .sep { color: var(--white); margin: 0 4px; }

  /* Back side */
  .card-back {
    background: var(--card-back);
    display: flex;
    align-items: center;
    justify-content: center;
  }
  .back-name {
    color: var(--gold);
    font-weight: 300;
    font-size: 18px;
    letter-spacing: 3px;
  }
</style>
</head>
<body>
  <main class="stage">
    <section class="card card-front">
      <div class="brand">
        <div class="brand-row">
          <span class="brand-mark"></span>
          <span class="brand-name">CLEARLINE STUDIO</span>
        </div>
        <span class="brand-tagline">Architecture Corporate Commercial</span>
      </div>
      <div class="rule rule-top"></div>
      <div class="contact">
        <p class="person-name">MARCUS HALE</p>
        <p class="person-title">Managing Director</p>
        <div class="contact-rule"></div>
        <p class="contact-line">18 Harbour Row, Eastfield, 30217</p>
        <div class="contact-rule"></div>
        <p class="contact-line">
          <span class="label">P:</span> 021-555 018 442<span class="sep">|</span><span class="label">E:</span>hello@clearline.com<span class="sep">|</span><span class="web">www.clearlinephoto.com</span>
        </p>
      </div>
    </section>

    <section class="card card-back" role="img" aria-label="Faint repeated brand-icon pattern across a dark card back">
      <span class="back-name">CLEARLINE STUDIO</span>
    </section>
  </main>
</body>
</html>
```